Ram and co fleecing works pty ltd

We are sheep shearing contractors,we are looking for a simple design business card, with a drawing like picture of a Australian sheep on it, then just standard details, name, phone, email, po box.
We would like double sided, with 2 lines of wiriting on the back, no bright colours please.
We like black and white, doesn't have to be too serious, however nothing to far left of cwntre.
On the back of the card we would like professional shearing contract offering full contract team.
Can use use the symbol & in the name instead of and.

Target Market(s)

Sheep farmers, target males from age 20 and up

Contact Information for Business Card

Company name ram and co fleecing works pty ltd
Marcus haldenby 0471305846, po box 4072 sale vic 3853,
Email ramandcofleecing@mailbarn.example, gippsland shearing contractor

Font styles to use
Serif

Colors

Designer to choose only greyscale colors for use in the design.

Requirements
Nice to have
• Simple design

```html
<!DOCTYPE html>
<html lang="en">
<head>
<meta charset="utf-8">
<title>Ram and Co Fleecing Works — Business Card</title>
<link href="https://fonts.googleapis.com/css2?family=Archivo:wght@400;700&display=swap" rel="stylesheet">
<style>
  :root {
    --backdrop: #111112;
    --card-dark: #2b2b2d;
    --card-dark-edge: #1f1f21;
    --card-light: #f2f2f2;
    --ink-light: #ffffff;
    --ink-soft: #e4e4e4;
    --ink-dark: #1b1b1b;
    --rule-dark: #bdbdbd;
    --rule-light: #9a9a9a;
    --art-1: #6a6a6c;
    --art-2: #3a3a3c;
  }
  * { box-sizing: border-box; margin: 0; padding: 0; }
  html, body { width: 1200px; height: 820px; overflow: hidden; }
  body {
    background: var(--backdrop);
    font-family: "Archivo", Arial, sans-serif;
    display: flex;
    align-items: center;
    justify-content: center;
    gap: 40px;
  }
  .card {
    position: relative;
    width: 560px;
    height: 320px;
    border-radius: 4px;
    overflow: hidden;
  }

  /* Front */
  .card--front {
    background: linear-gradient(160deg, var(--card-dark) 0%, var(--card-dark-edge) 100%);
    color: var(--ink-light);
  }
  .front__artwork {
    position: absolute;
    right: 0;
    top: 0;
    width: 270px;
    height: 230px;
    background: radial-gradient(ellipse at 55% 45%, var(--art-1) 0%, var(--art-2) 60%, transparent 78%);
    opacity: 0.85;
  }
  .brand {
    position: absolute;
    left: 40px;
    top: 46px;
    width: 300px;
  }
  .brand__name {
    font-weight: 700;
    font-size: 30px;
    line-height: 1.02;
    letter-spacing: 0.5px;
    text-transform: uppercase;
    color: var(--ink-light);
  }
  .brand__rule {
    height: 1px;
    background: var(--rule-dark);
    margin-top: 10px;
    width: 280px;
  }
  .contact {
    position: absolute;
    left: 40px;
    top: 176px;
  }
  .contact__name {
    font-weight: 700;
    font-size: 17px;
    letter-spacing: 1px;
    text-transform: uppercase;
    margin-bottom: 12px;
  }
  .contact__line {
    display: flex;
    align-items: center;
    gap: 9px;
    font-size: 15px;
    color: var(--ink-soft);
    line-height: 1.45;
  }
  .contact__line svg { width: 14px; height: 14px; flex: none; }
  .contact__address {
    font-size: 15px;
    color: var(--ink-soft);
    margin-top: 14px;
  }

  /* Back */
  .card--back {
    background: var(--card-light);
    color: var(--ink-dark);
    box-shadow: 0 0 0 1px #d8d8d8 inset;
  }
  .back__lockup {
    position: absolute;
    left: 44px;
    top: 44px;
    display: flex;
    align-items: center;
    gap: 16px;
  }
  .back__mark {
    width: 70px;
    height: 70px;
    border-radius: 50%;
    background: var(--ink-dark);
    flex: none;
  }
  .back__name {
    font-weight: 700;
    font-size: 22px;
    line-height: 1.05;
    text-transform: uppercase;
    width: 270px;
  }
  .back__rule {
    height: 1px;
    background: var(--ink-dark);
    width: 250px;
    margin-top: 8px;
  }
  .back__tagline {
    font-size: 13px;
    margin-top: 6px;
  }
  .write-line {
    position: absolute;
    left: 160px;
    width: 360px;
    height: 1px;
    background: var(--rule-light);
  }
  .write-line--one { top: 160px; }
  .write-line--two { top: 210px; }
  .back__offer {
    position: absolute;
    left: 44px;
    bottom: 40px;
    font-size: 15px;
  }
</style>
</head>
<body>

  <section class="card card--front">
    <div class="front__artwork" role="img" aria-label="Illustration of a sheep in mid-stride, shown as a faint grey silhouette"></div>

    <div class="brand">
      <p class="brand__name">Ram and Co<br>Fleecing Works<br>Pty Ltd</p>
      <div class="brand__rule"></div>
    </div>

    <div class="contact">
      <p class="contact__name">Marcus Haldenby</p>
      <p class="contact__line">
        <svg viewBox="0 0 16 16" aria-hidden="true"><path fill="#fff" d="M3.6 1.5 6 4.2 4.8 5.8c.8 1.9 2.4 3.5 4.3 4.3l1.6-1.2 2.7 2.4-1.3 2.2c-5.6-.5-10-5-10.5-10.5z"/></svg>
        0471305846
      </p>
      <p class="contact__line">
        <svg viewBox="0 0 16 16" aria-hidden="true"><rect x="1" y="3" width="14" height="10" fill="none" stroke="#fff" stroke-width="1.4"/><path d="M1 3l7 6 7-6" fill="none" stroke="#fff" stroke-width="1.4"/></svg>
        ramandcofleecing@mailbarn.example
      </p>
      <p class="contact__address">PO box 4072 sale vic 3853</p>
    </div>
  </section>

  <section class="card card--back">
    <div class="back__lockup">
      <div class="back__mark"></div>
      <div>
        <p class="back__name">Ram and Co Fleecing Works Pty Ltd</p>
        <div class="back__rule"></div>
        <p class="back__tagline">Gippsland shearing contractor</p>
      </div>
    </div>
    <div class="write-line write-line--one"></div>
    <div class="write-line write-line--two"></div>
    <p class="back__offer">Professional shearing contract offering full contract team.</p>
  </section>

</body>
</html>
```